Nimbo31.com.au Website and company image design

We are looking for an exceptional website designer / company to work with our new Australian Hosting Company

Nimbo31 is a new Cloud Hosting company launching in Australia that provides Scalable, On Demand computing resources to the Australian Market Place. Scalable, On Demand ocmputing is a nice way of saying fully scalable / redundant Virtual Private Server.

We require a full company image to be developed along with a Logo and Website. There is scope for ongoing development (preferred) for the successful candidate.

Website developement will require extensive jQuery ability (sliders for ordering etc (see: http://www.hostrivo.com.au/virtual-dedicated-servers/253/kelp_vps.html).

Please communicate directly with me to establish full website scope and request further documentation / content.

Target Market(s)

Website Designers, programmers, technicians and large companies

Industry/Entity Type

It Company

Requirements
Must have
• Slider ordering system such as http://www.hostrivo.com.au/virtual-dedicated-servers/253/kelp_vps.html

Nice to have
• CMS backend system
Should not have
• Should NOT be a monster template copy!!!

```html
<!DOCTYPE html>
<html lang="en">
<head>
<meta charset="utf-8">
<title>Nimbo31 — Cloud Hosting</title>
<link href="https://fonts.googleapis.com/css2?family=Source+Sans+3:ital,wght@0,300;0,400;0,600;0,700;1,400&family=Ubuntu:wght@300;400;500&display=swap" rel="stylesheet">
<style>
:root{
  --maroon:#8c1f45;
  --maroon-dark:#74173a;
  --ink:#333;
  --text:#555;
  --muted:#888;
  --topbar:#2b2f38;
  --panel:#ececec;
  --line:#dcdcdc;
  --white:#fff;
}
*{margin:0;padding:0;box-sizing:border-box}
html,body{width:1200px;height:2203px;overflow:hidden}
body{position:relative;background:#fff;font-family:"Source Sans 3",Arial,sans-serif;color:var(--text)}
.abs{position:absolute}

/* top bar */
.topbar{left:0;top:0;width:1200px;height:45px;background:var(--topbar)}
.topbar a{position:absolute;top:14px;color:#fff;font-size:13px;text-decoration:none;display:flex;align-items:center;gap:8px;white-space:nowrap}
.topbar svg{width:14px;height:14px;fill:#fff}

/* header */
.header{left:0;top:45px;width:1200px;height:135px;background:linear-gradient(#f4f4f4,#fafafa)}
.brand{left:108px;top:60px;display:flex;align-items:center;gap:12px}
.brand-dot{width:70px;height:70px;border-radius:50%;background:var(--maroon)}
.brand-name{font-family:"Ubuntu",sans-serif;font-weight:500;font-size:46px;color:var(--maroon);white-space:nowrap}
.nav{left:353px;top:88px;width:755px;height:28px;border-bottom:2px solid var(--maroon)}
.nav-item{position:absolute;top:2px;font-family:"Ubuntu",sans-serif;font-size:14px;color:var(--maroon);text-transform:uppercase;white-space:nowrap}
.nav-sep{position:absolute;top:0;width:1px;height:22px;background:var(--maroon)}
.nav-sub{position:absolute;top:126px;font-size:12px;color:#333;white-space:nowrap}
.header-rule{left:111px;top:173px;width:979px;height:1px;background:#e2e2e2}

/* hero */
.hero{left:0;top:180px;width:1200px;height:270px;background:linear-gradient(#fafafa,#ececec 85%,#fff)}
.hero-art{left:170px;top:200px;width:255px;height:250px;border-radius:4px;background:linear-gradient(110deg,#1e2128,#6b6f78 45%,#2a2d33)}
.hero-title{left:443px;top:222px;font-family:"Ubuntu",sans-serif;font-weight:300;font-size:50px;color:#444;white-space:nowrap}
.hero-points{left:448px;top:305px;font-size:13px;color:#555;display:flex;gap:14px;white-space:nowrap}
.hero-btn{left:882px;top:300px;width:185px;height:28px;background:#c9c9c9;color:#fff;font-size:13px;display:flex;align-items:center;justify-content:center;white-space:nowrap}
.dot{position:absolute;top:396px;width:18px;height:18px;border-radius:50%;border:1px solid #ccc;background:#fff;font-size:10px;color:#555;display:flex;align-items:center;justify-content:center}
.dot.active{border-color:var(--maroon)}

/* plans */
.plan{top:505px;width:314px;height:518px;background:#f8f8f8}
.plan-head{height:63px;display:flex;align-items:center;gap:14px;padding-left:30px;font-family:"Ubuntu",sans-serif;font-size:22px;color:#333;text-transform:uppercase;border-top:3px solid #bdbdbd;background:#fff;white-space:nowrap}
.plan.featured .plan-head{background:var(--maroon);color:#fff;border-top-color:var(--maroon)}
.plan-head svg{width:30px;height:30px}
.plan-list{list-style:none;margin:22px 0 0 40px}
.plan-list li{height:30px;font-size:13px;color:#666;display:flex;align-items:center;gap:16px;white-space:nowrap}
.plan-list svg{width:14px;height:10px;fill:#999}
.plan-price{position:absolute;top:262px;left:0;width:100%;text-align:center;font-size:17px;color:#333;white-space:nowrap}
.plan-price b{font-size:33px;font-weight:600;margin-left:10px;vertical-align:-4px}
.plan.featured .plan-price b{color:var(--maroon)}
.plan-btn{position:absolute;top:315px;left:48px;width:218px;height:35px;background:#dedede;color:#444;font-size:14px;display:flex;align-items:center;justify-content:center;gap:10px}
.plan-specs{position:absolute;top:350px;left:0;width:100%;height:168px;background:#f1f1f1;border-top:2px solid #fff;padding-top:20px;text-align:center}
.plan.featured .plan-specs{background:#e3e3e3}
.plan-specs p{font-size:12.5px;color:#555;line-height:26px;white-space:nowrap}

/* hybrid */
.section-title{font-family:"Ubuntu",sans-serif;font-weight:400;font-size:19px;color:#333;white-space:nowrap}
.hybrid-rule{left:111px;top:1102px;width:647px;height:1px;background:var(--line)}
.hybrid-tag{left:113px;top:1118px;font-size:15px;color:var(--maroon);white-space:nowrap}
.hybrid-tag b{font-size:19px;font-weight:600;margin-left:8px}
.hybrid-copy{left:113px;top:1151px;width:645px;font-size:12.5px;line-height:20px;color:#555}
.offer{left:776px;top:1067px;width:314px;height:146px;background:linear-gradient(100deg,#f2f2f2 10%,#6d6f74 55%,#1d1f23)}
.offer-btn{position:absolute;right:0;bottom:14px;width:150px;height:28px;border-radius:14px 0 0 14px;background:rgba(40,40,40,.85);color:#fff;font-size:14px;display:flex;align-items:center;justify-content:center;white-space:nowrap}

/* why us */
.why-intro{left:113px;top:1290px;width:977px;font-size:12px;line-height:20px;color:#444}
.why-box{left:115px;top:1338px;width:973px;height:355px;border:1px solid var(--line);background:#fff}
.why-copy{position:absolute;left:23px;top:22px;width:707px;font-size:12.5px;line-height:20px;color:#555}
.tabs{position:absolute;right:0;top:0;width:215px;height:353px;background:#f1f1f1;border-left:1px solid var(--line)}
.tab{height:41px;display:flex;align-items:center;padding-left:40px;font-size:14px;color:#666;border-bottom:1px solid #e2e2e2;white-space:nowrap}
.tab.active{background:#fff;color:#333;margin-left:-1px}
.tab:first-child{margin-top:10px}
.feature{position:absolute;width:225px}
.feature h4{font-size:11.5px;font-weight:600;color:var(--maroon);white-space:nowrap}
.feature p{font-size:9.5px;line-height:15px;color:#999;margin-top:2px}

/* testimonial */
.avatar{left:120px;top:1725px;width:83px;height:90px;border:2px solid #e5e5e5;background:linear-gradient(#f1d9c4,#c99e80)}
.avatar-name{left:112px;top:1825px;width:100px;text-align:center;font-size:13px;color:var(--maroon);white-space:nowrap}
.bubble{left:228px;top:1725px;width:855px;height:115px;background:#f2f2f2}
.bubble:before{content:"";position:absolute;left:-12px;top:20px;border:12px solid transparent;border-left:0;border-right-color:#f2f2f2}
.bubble h3{position:absolute;left:18px;top:14px;font-family:"Ubuntu",sans-serif;font-weight:400;font-size:19px;color:#333;white-space:nowrap}
.bubble blockquote{position:absolute;left:20px;top:55px;width:810px;font-style:italic;font-size:13px;line-height:21px;color:#555}

/* feed band */
.feed{left:0;top:1872px;width:1200px;height:86px;background:#f1f1f1}
.feed-title{position:absolute;left:198px;top:22px;font-family:"Ubuntu",sans-serif;font-weight:500;font-size:32px;color:#555;white-space:nowrap}
.feed-text{position:absolute;left:451px;top:24px;width:630px;font-size:13px;line-height:20px;color:#333}

/* footer */
.footer{left:0;top:1958px;width:1200px;height:185px;background:linear-gradient(#e2e2e2,#ececec)}
.fcol{position:absolute;top:38px}
.fcol h5{font-size:14px;font-weight:400;color:var(--maroon);margin-bottom:8px;white-space:nowrap}
.fcol li{list-style:none;font-size:12px;line-height:20px;color:#444;white-space:nowrap}
.fbrand{position:absolute;left:812px;top:50px;display:flex;align-items:center;gap:8px}
.fbrand span:first-child{width:44px;height:44px;border-radius:50%;background:#bdbdbd}
.fbrand span:last-child{font-family:"Ubuntu",sans-serif;font-weight:500;font-size:28px;color:#9a9a9a;white-space:nowrap}
.fabout{position:absolute;left:812px;top:118px;width:275px;font-size:11px;line-height:16px;color:#555}
.social{position:absolute;top:64px;width:24px;height:24px;border-radius:3px}
.bottom{left:0;top:2143px;width:1200px;height:60px;background:#d5d5d5;font-size:11px;color:#444;text-align:center;line-height:60px;white-space:nowrap}
</style>
</head>
<body>

<div class="abs topbar">
  <a style="left:438px"><svg viewBox="0 0 16 16"><path d="M3 1l3 3-2 2c1 2 3 4 5 5l2-2 3 3-2 3C7 15 1 9 1 3z"/></svg>888-9-nimbo31</a>
  <a style="left:588px"><svg viewBox="0 0 16 16"><path d="M8 2c4 0 7 2 7 5s-3 5-7 5l-4 3 1-4C3 10 1 9 1 7c0-3 3-5 7-5z"/></svg>Live Chat</a>
  <a style="left:715px"><svg viewBox="0 0 16 16"><path d="M1 6l7-4 7 4v8H1z"/></svg>Email Us</a>
  <a style="left:845px"><svg viewBox="0 0 16 16"><path d="M2 3h7v2H4v7h7V8h2v6H2zM12 1l3 3-6 6H6V7z"/></svg>Get a Quote</a>
  <a style="left:993px"><svg viewBox="0 0 16 16"><circle cx="8" cy="5" r="3.5"/><path d="M1 15c0-4 3-6 7-6s7 2 7 6z"/></svg>Client Login</a>
</div>

<div class="abs header"></div>
<div class="abs brand"><span class="brand-dot"></span><span class="brand-name">Nimbo31</span></div>
<nav class="abs nav">
  <span class="nav-item" style="left:85px">Dedicated Servers</span>
  <span class="nav-sep" style="left:255px"></span>
  <span class="nav-item" style="left:285px">Virtual Servers</span>
  <span class="nav-sep" style="left:433px"></span>
  <span class="nav-item" style="left:465px">Cloud Servers</span>
  <span class="nav-sep" style="left:606px"></span>
  <span class="nav-item" style="left:630px">About Nimbo31</span>
</nav>
<span class="abs nav-sub" style="left:438px">Met Kestrel Servers</span>
<span class="abs nav-sub" style="left:639px">OpenKel or Kelp</span>
<span class="abs nav-sub" style="left:818px">Vireo Enterprise</span>
<span class="abs nav-sub" style="left:991px">Learn about us</span>
<div class="abs header-rule"></div>

<section class="abs hero"></section>
<div class="abs hero-art" role="img" aria-label="Illustration of three dark server towers with blue lights"></div>
<h1 class="abs hero-title">why we're different?</h1>
<div class="abs hero-points"><span>Fast response times</span><span>|</span><span>Your needs Matter</span><span>|</span><span>Enterprise Solutions</span></div>
<div class="abs hero-btn">More about our services</div>
<span class="dot active" style="left:921px">1</span>
<span class="dot" style="left:961px">2</span>
<span class="dot" style="left:1001px">3</span>
<span class="dot" style="left:1041px">4</span>

<article class="abs plan featured" style="left:111px">
  <div class="plan-head"><svg viewBox="0 0 30 30"><rect x="9" y="2" width="12" height="26" fill="#fff"/><rect x="11" y="6" width="8" height="2" fill="#8c1f45"/><rect x="11" y="10" width="8" height="2" fill="#8c1f45"/></svg>Dedicated Servers</div>
  <ul class="plan-list">
    <li><svg viewBox="0 0 14 10"><path d="M0 3h8V0l6 5-6 5V7H0z"/></svg>Enterprise MicroForge Servers</li>
    <li><svg viewBox="0 0 14 10"><path d="M0 3h8V0l6 5-6 5V7H0z"/></svg>Fully Customized Configurations</li>
    <li><svg viewBox="0 0 14 10"><path d="M0 3h8V0l6 5-6 5V7H0z"/></svg>Ready in hours</li>
    <li><svg viewBox="0 0 14 10"><path d="M0 3h8V0l6 5-6 5V7H0z"/></svg>Kestrel Core Processors</li>
    <li><svg viewBox="0 0 14 10"><path d="M0 3h8V0l6 5-6 5V7H0z"/></svg>IPMI Remote Management</li>
  </ul>
  <div class="plan-price">Starting at <b>$99/mo</b></div>
  <div class="plan-btn">Learn More <span>&gt;&gt;</span></div>
  <div class="plan-specs"><p>Hardware Raid w/ Battery Backup</p><p>Up to 32GB Ram</p><p>Up to 16 Hot swap hard drives</p><p>SSD, SAS and SATA drive options</p><p>Any Operating System</p></div>
</article>

<article class="abs plan" style="left:444px">
  <div class="plan-head"><svg viewBox="0 0 30 30"><path d="M7 24a6 6 0 010-12 8 8 0 0115-2 6 6 0 011 14z" fill="#333"/></svg>Cloud Servers</div>
  <ul class="plan-list">
    <li><svg viewBox="0 0 14 10"><path d="M0 3h8V0l6 5-6 5V7H0z"/></svg>Vireo Cloud</li>
    <li><svg viewBox="0 0 14 10"><path d="M0 3h8V0l6 5-6 5V7H0z"/></svg>Fully redundant 100% uptime</li>
    <li><svg viewBox="0 0 14 10"><path d="M0 3h8V0l6 5-6 5V7H0z"/></svg>Enterprise Ready</li>
  </ul>
  <div class="plan-price">Starting at <b>$99/mo</b></div>
  <div class="plan-btn">Learn More <span>&gt;&gt;</span></div>
  <div class="plan-specs"><p>Hardware Raid w/ Battery Backup</p><p>Up to 32GB Ram</p><p>Up to 16 Hot swap hard drives</p><p>SSD, SAS and SATA drive options</p><p>Any Operating System</p></div>
</article>

<article class="abs plan" style="left:776px">
  <div class="plan-head"><svg viewBox="0 0 30 30" fill="#333"><rect x="11" y="2" width="8" height="7"/><rect x="14" y="9" width="2" height="6"/><rect x="4" y="14" width="22" height="2"/><rect x="4" y="14" width="2" height="6"/><rect x="24" y="14" width="2" height="6"/><rect x="1" y="20" width="8" height="7"/><rect x="21" y="20" width="8" height="7"/></svg>VPS Hosting</div>
  <ul class="plan-list">
    <li><svg viewBox="0 0 14 10"><path d="M0 3h8V0l6 5-6 5V7H0z"/></svg>OpenKel or Kelp</li>
    <li><svg viewBox="0 0 14 10"><path d="M0 3h8V0l6 5-6 5V7H0z"/></svg>Ready in minutes</li>
    <li><svg viewBox="0 0 14 10"><path d="M0 3h8V0l6 5-6 5V7H0z"/></svg>Affordable and reliable</li>
  </ul>
  <div class="plan-price">Starting at <b>$99/mo</b></div>
  <div class="plan-btn">Learn More <span>&gt;&gt;</span></div>
  <div class="plan-specs"><p>Hardware Raid w/ Battery Backup</p><p>Up to 32GB Ram</p><p>Up to 16 Hot swap hard drives</p><p>SSD, SAS and SATA drive options</p><p>Any Operating System</p></div>
</article>

<h2 class="abs section-title" style="left:112px;top:1064px">Hybrid Solutions</h2>
<div class="abs hybrid-rule"></div>
<p class="abs hybrid-tag">The best of both dedicated and cloud. <b>$179/mo</b></p>
<p class="abs hybrid-copy">Ut enim ad minim veniam, quis nostrud exercitation ullamco laboris nisi ut aliquip ex ea commodo consequat. Duis aute irure dolor in reprehenderit in voluptate velit esse cillum dolore eu fugiat nulla pariatur. Excepteur sint occaecat cupida tat non proident, sunt in culpa qui officia deserunt mollit anim id est laborum.</p>
<div class="abs offer" role="img" aria-label="Special offers banner showing rows of server racks">
  <div class="offer-btn">View more Details</div>
</div>

<h2 class="abs section-title" style="left:112px;top:1248px">Why Us?</h2>
<p class="abs why-intro">The service we offer is different and our approach is unique. We exceed every industry standard while remaining price competitive. Below are the top differentiators from the rest of the industry. Please see The Corvane Difference for a comprehensive list.</p>
<div class="abs why-box">
  <p class="why-copy">Lorem ipsum dolor sit amet, consectetur adipiscing elit. Duis feugiat rutrum luctus. Proin nisl augue, tempus quis lacinia at, ultrices eget sapien. Vestibulum at orci a eros molestie rutrum. Fusce interdum erat vel eros elementum vitae interdum massa varius. Morbi fermentum commodo nisi, id interdum mauris suscipit pellentesque. Morbi velit eros, accumsan ut faucibus at, viverra id mi. Nunc augue nisl, rutrum vitae luctus nec, lobortis sit amet diam. Proin porttitor semper sollicitudin. Donec mollis rhoncus turpis et rhon cus. In elit nisl, ultrices id mollis ut, dapibus eget nulla. Fusce laoreet neque ut purus faucibus ut condimentum purus condimentum. Vestibulum vel magna ligula, in tincidunt augue.</p>
  <div class="feature" style="left:24px;top:183px"><h4>SSAE 16 SOC-1 Type II Compliant Facility</h4><p>Independent third-party audits confirm integrity, reliability, effectiveness and security of the facility</p></div>
  <div class="feature" style="left:278px;top:183px"><h4>Multiple Fiber Entrances</h4><p>Cables enter at more than one point to guard against outages caused by cut lines</p></div>
  <div class="feature" style="left:534px;top:183px"><h4>24/7 On-site Staff for Security</h4><p>Staff on site keep the facility and hardware safe from unauthorized access</p></div>
  <div class="feature" style="left:24px;top:248px"><h4>Security Cameras</h4><p>The building is watched by many cameras to record all activity</p></div>
  <div class="feature" style="left:278px;top:248px"><h4>Premiter Fence with Gates</h4><p>The building is enclosed by a fence and gates that stop unauthorized entry</p></div>
  <div class="feature" style="left:534px;top:248px"><h4>Card Key Access</h4><p>Electronic doors open only with physical card keys to block unauthorized access</p></div>
  <div class="tabs">
    <div class="tab">Network</div><div class="tab active">Facility</div><div class="tab">Support</div><div class="tab">Firewall</div><div class="tab">VPN Access</div><div class="tab">Servers</div><div class="tab">Remote Server Control</div><div class="tab">SLA</div>
  </div>
</div>

<div class="abs avatar" role="img" aria-label="Portrait photo of customer Daniel Crane"></div>
<div class="abs avatar-name">Daniel Crane</div>
<div class="abs bubble">
  <h3>Customer Testimonials</h3>
  <blockquote>&ldquo; Vestibulum at orci a eros molestie rutrum. Fusce interdum erat vel eros elementum vitae interdum massa varius. Morbi fermentum commodo nisi, id interdum mauris suscipit pellentesque. Morbi velit eros, accumsan ut faucibus at, viverra id mi. &rdquo;</blockquote>
</div>

<section class="abs feed">
  <div class="feed-title">Chirpline Feeds</div>
  <p class="feed-text">Sed ut perspiciatis unde omnis iste natus error sit <u>voluptatem accusantium doloremque laudantium</u>, totam rem ape riam, eaque ipsa quae.</p>
</section>

<footer class="abs footer">
  <div class="fcol" style="left:121px"><h5>Main Navigation</h5><ul><li>Dedicated Servers</li><li>Virtual Servers</li><li>l Cloud Servers</li><li>About Nimbo31</li></ul></div>
  <div class="fcol" style="left:285px"><h5>Additional Info</h5><ul><li>Terms of Service</li><li>Privacy Policy</li><li>Service Level Agreement</li><li>Referral Program</li><li>l Reseller Program</li></ul></div>
  <div class="fcol" style="left:492px"><h5>Support Center</h5><ul><li>USA 888-9-nimbo31</li><li>Live Chat</li><li>Email Us</li><li>Get a Quote</li><li>Client Login</li></ul></div>
  <div class="fcol" style="left:653px"><h5>Locations</h5><ul><li>Chicago, IL</li><li>Dallas, TX</li><li>Kansas City, MO</li><li>Los Angeles, CA</li><li>New York City, NY</li></ul></div>
  <div class="fbrand"><span></span><span>Nimbo31</span></div>
  <p class="fabout">We are a company at technical people, not sales drones. We deliver data center services to You</p>
  <span class="social" style="left:1018px;background:#3b5a98"></span>
  <span class="social" style="left:1055px;background:#4fb6e8"></span>
</footer>
<div class="abs bottom">Copyright © 2012 www.nimbo31.com.au &nbsp;&nbsp;All rights reserved.</div>

</body>
</html>
```